KAJU Freightways #ALLKAJU Business Cards & Letterhead

I am looking to business cards designed for our organization. We are currently undergoing a small re-branding that is taking place. Our organization is called KAJU Freightways and we are headquartered in Phoenix, AZ. We primarily provide transportation and logistics services to the Marlow Parcel Bureau who is our largest customer. I would like to see a design that incorporates name, title, contact info, website, and address (this will be different depending on the employee). I would also like to see some color on the business card using our logo colors or a variation. I would like our logo on the back of the business card with the website displayed. The final design should communicate that we are a next generation transportation operate that focuses on being driver-first, customer-centric, innovative, and sustainable.We would also like our #ALLKAJU catch phrase incorporated as well.

Target Market(s)

Transportation & Logistics

Industry/Entity Type

Trucking Company

Contact Information for Business Card

-First and Last Name
-Position Title
-Contact Phone
-Contact Email
-Physical Address

Font styles to use
Serif

Colors

Designer to choose colors to be used in the design.

Requirements
Must have
• -KAJU logo prominently displayed
• -#ALLKAJU catch phrase used
• -Some amount of color, design gradient, etc.
• -Logo on the back with website listed (https://www.kajufreightco.example)

```html
<!DOCTYPE html>
<html lang="en">
<head>
<meta charset="utf-8">
<title>KAJU Freightways Business Card</title>
<link href="https://fonts.googleapis.com/css2?family=Montserrat:wght@400;700;800&display=swap" rel="stylesheet">
<style>
  :root {
    --bg: #a9a9ab;
    --paper: #ffffff;
    --teal-dark: #022f38;
    --teal-light: #02606b;
    --brand-green: #66bb36;
    --brand-navy: #0d3a44;
    --silver: #c9ccce;
    --muted: #9fb0b4;
    --rule: #6f9aa0;
    --pattern: #eef4ea;
    --body-text: #dfe8ea;
  }
  * { box-sizing: border-box; margin: 0; padding: 0; }
  html, body { width: 1200px; height: 960px; overflow: hidden; }
  body {
    background: var(--bg);
    font-family: "Montserrat", Arial, sans-serif;
    position: relative;
  }
  .card {
    position: absolute;
    width: 700px;
    height: 400px;
    box-shadow: 0 10px 30px rgba(0,0,0,0.25);
    overflow: hidden;
  }

  /* Front */
  .card-front {
    left: 60px; top: 60px;
    background: var(--paper);
  }
  .pattern-area {
    position: absolute; inset: 0;
    background: radial-gradient(circle at 50% 50%, var(--paper) 0 30%, var(--pattern) 70%, #f3f5f4 100%);
  }
  .front-brand {
    position: absolute;
    left: 0; right: 0; top: 160px;
    display: flex; align-items: center; justify-content: center; gap: 14px;
  }
  .front-brand .brand-dot {
    width: 22px; height: 22px; border-radius: 50%;
    background: var(--brand-green);
  }
  .front-brand .brand-name {
    font-weight: 800;
    font-size: 58px;
    line-height: 1;
    color: var(--brand-navy);
    letter-spacing: 1px;
  }
  .tagline {
    position: absolute;
    left: 0; right: 0; top: 236px;
    text-align: center;
    font-weight: 700;
    font-size: 16px;
    letter-spacing: 3px;
    color: var(--brand-green);
  }

  /* Back */
  .card-back {
    left: 440px; top: 500px;
    background: linear-gradient(200deg, var(--teal-light) 0%, var(--teal-dark) 100%);
    color: #fff;
  }
  .back-brand {
    position: absolute;
    right: 56px; top: 70px;
    display: flex; align-items: center; gap: 12px;
  }
  .back-brand .brand-dot {
    width: 16px; height: 16px; border-radius: 50%;
    background: var(--silver);
  }
  .back-brand .brand-name {
    font-weight: 800;
    font-size: 44px;
    line-height: 1;
    color: var(--silver);
    letter-spacing: 1px;
  }
  .person-name {
    position: absolute; left: 48px; top: 196px;
    font-weight: 800; font-size: 24px; line-height: 1.2;
    color: var(--brand-green);
    letter-spacing: 0.5px;
  }
  .person-title {
    position: absolute; left: 48px; top: 228px;
    font-size: 15px; color: var(--muted);
  }
  .contact-list {
    position: absolute; left: 48px; top: 260px;
    list-style: none;
    font-size: 15px; color: var(--body-text);
  }
  .contact-list li {
    display: flex; align-items: center; gap: 10px;
    height: 22px;
  }
  .icon { width: 13px; height: 13px; fill: var(--brand-green); flex: none; }
  .divider {
    position: absolute; left: 48px; right: 36px; top: 334px;
    height: 1px; background: var(--rule);
  }
  .address {
    position: absolute; left: 48px; top: 348px;
    display: flex; align-items: center; gap: 10px;
    font-size: 15px; color: var(--body-text);
  }
</style>
</head>
<body>

<section class="card card-front">
  <div class="pattern-area" role="img" aria-label="Faint repeating brand pattern in pale grey and green"></div>
  <div class="front-brand">
    <span class="brand-dot"></span>
    <span class="brand-name">KAJU</span>
  </div>
  <p class="tagline">#ALLKAJU</p>
</section>

<section class="card card-back">
  <div class="back-brand">
    <span class="brand-dot"></span>
    <span class="brand-name">KAJU</span>
  </div>

  <h1 class="person-name">DANIEL REYES</h1>
  <p class="person-title">President</p>

  <ul class="contact-list">
    <li>
      <svg class="icon" viewBox="0 0 16 16"><path d="M3 1l3 3-1.6 2a9 9 0 0 0 5.6 5.6L12 10l3 3-2 2C6 15 1 10 1 3z"/></svg>
      480-555-0172
    </li>
    <li>
      <svg class="icon" viewBox="0 0 16 16"><path d="M1 3h14v10H1z M1 3l7 6 7-6" fill="none" stroke="#66bb36" stroke-width="2"/></svg>
      daniel@kajufreightco.example
    </li>
    <li>
      <svg class="icon" viewBox="0 0 16 16"><circle cx="8" cy="8" r="7"/><path d="M1 8h14M8 1c3 3 3 11 0 14M8 1c-3 3-3 11 0 14" fill="none" stroke="#022f38" stroke-width="1.2"/></svg>
      www.kajufreightco.example
    </li>
  </ul>

  <div class="divider"></div>

  <p class="address">
    <svg class="icon" viewBox="0 0 16 16"><path d="M8 0a6 6 0 0 0-6 6c0 4.5 6 10 6 10s6-5.5 6-10a6 6 0 0 0-6-6zm0 8.5A2.5 2.5 0 1 1 8 3.5a2.5 2.5 0 0 1 0 5z"/></svg>
    2140 Saguaro Drive Phoenix, Arizona 85004
  </p>
</section>

</body>
</html>
```